Zilata - Sketches from a quiet road

🎨 Design Guidelines
1. Overall Impression

Dignified, spiritual, timeless

Central focus on sand dunes with footsteps as the main motif

Mood: calm, light, spirituality, hope

2. Color Scheme

Background: warm sand tones (beige, golden, brown)

Light source (sun/beam): soft gold/white

Typography: gold or warm yellow, metallic effect preferred (gold foil in print)

Spine and back cover: darker gradient from sand tones to deep blue/black for strong readability

3. Imagery

Front cover: sand dunes with clear footsteps leading towards light/horizon

No figurative depictions of people

Optional: subtle Islamic ornaments or geometric borders as a background accent

4. Typography

Title: “Zīlāta” → large, serif font, elegant, in gold

Subtitle: “Sketches From A Quiet Road” → smaller, clean & modern, also gold/white

Author: Idrīs-Wahīd Salmūn Qāzinī → bottom of the front cover, smaller size

Spine: Title + Arabic word زيلاتة vertically placed, harmonized with the style

5. Back Cover

Short blurb/description (provided by client)

Highlighted keywords in large type: "Courage. Integrity. Faith."

ISBN + barcode at the bottom left

Background: continuation of the sand texture from the front cover (with or without footsteps)

6. Finishing Options (Print)

Gold foil stamping for the title

Matte cover with selective gloss (eg on the light or ornaments)

High-quality, sturdy cover stock

Target Market(s)

Islamic

Font styles to use
Serif

Requirements
Must have
• read the guidelines!
Nice to have
• read the guidelines!
Should not have
• read the guidelines!

```html
<!DOCTYPE html>
<html lang="en">
<head>
<meta charset="utf-8">
<title>Zīlāta – Book Cover Wrap</title>
<link rel="stylesheet" href="https://fonts.googleapis.com/css2?family=Playfair+Display:wght@500;600&family=Open+Sans:wght@400&family=Lato:ital,wght@1,400&family=Tinos:wght@700&family=Noto+Naskh+Arabic:wght@500&display=swap">
<style>
  :root {
    --page: #ffffff;
    --navy-deep: #0e1a2b;
    --navy: #1f2b3d;
    --navy-soft: #2a3547;
    --gold-light: #fff3b0;
    --gold: #e9c760;
    --gold-dark: #6e5514;
    --gold-text: #f6dd7a;
    --subtitle-brown: #a97a32;
    --sand-top: #fbf1dc;
    --sand-glow: #fff6e0;
    --sand-mid: #e6a93a;
    --sand-low: #c9801c;
    --sand-deep: #9e5510;
    --ink-light: #f4f1ea;
    --white: #ffffff;
  }
  * { margin: 0; padding: 0; box-sizing: border-box; }
  html, body { width: 1200px; height: 872px; overflow: hidden; background: var(--page); }

  .canvas { position: relative; width: 1200px; height: 872px; }
  .cover-wrap { position: absolute; left: 43px; top: 43px; width: 1114px; height: 786px; overflow: hidden; }

  /* Back cover */
  .back-cover { position: absolute; left: 0; top: 0; width: 521px; height: 786px; }
  .back-scene {
    position: absolute; inset: 0;
    background:
      radial-gradient(ellipse 60% 40% at 50% 30%, var(--navy-soft), transparent 70%),
      linear-gradient(180deg, var(--navy) 0%, #222c3b 55%, #1b2230 100%);
  }
  .back-title {
    position: absolute; left: 0; width: 521px; top: 145px; text-align: center;
    font-family: "Playfair Display", serif; font-weight: 500; font-size: 86px; line-height: 1;
  }
  .back-subtitle {
    position: absolute; left: 0; width: 521px; top: 240px; text-align: center;
    font-family: "Open Sans", sans-serif; font-size: 19px; letter-spacing: 5px; color: var(--gold-text);
  }
  .keywords {
    position: absolute; left: 34px; width: 456px; top: 299px;
    font-family: "Lato", sans-serif; font-style: italic; font-size: 34.5px; line-height: 1.1; letter-spacing: 0.5px;
    color: var(--gold-text); white-space: nowrap;
  }
  .blurb {
    position: absolute; font-family: "Open Sans", sans-serif; font-size: 12.8px; line-height: 16.6px;
    color: var(--ink-light); text-align: justify; hyphens: auto;
  }
  .blurb-main { left: 34px; width: 457px; top: 353px; text-align-last: center; }
  .blurb-side { left: 140px; width: 351px; top: 485px; text-align-last: left; }
  .author-photo { position: absolute; left: 33px; top: 485px; width: 96px; height: 115px; background: var(--white); }
  .isbn-box { position: absolute; left: 168px; top: 647px; width: 187px; height: 53px; background: var(--white); }

  /* Spine */
  .spine { position: absolute; left: 521px; top: 0; width: 69px; height: 786px; background: var(--navy-deep); }
  .spine-title {
    position: absolute; left: 14px; top: 169px; writing-mode: vertical-rl;
    font-family: "Playfair Display", serif; font-weight: 600; font-size: 40px; line-height: 1; color: var(--gold-text);
  }
  .spine-arabic {
    position: absolute; left: 14px; top: 512px; writing-mode: vertical-rl;
    font-family: "Noto Naskh Arabic", serif; font-size: 34px; line-height: 1; color: var(--gold-text);
  }

  /* Front cover */
  .front-cover { position: absolute; left: 590px; top: 0; width: 524px; height: 786px; }
  .front-scene {
    position: absolute; inset: 0;
    background:
      radial-gradient(ellipse 40% 22% at 45% 40%, var(--sand-glow) 0%, transparent 100%),
      linear-gradient(180deg, var(--sand-top) 0%, #f8e7c2 30%, #f2cf86 45%, var(--sand-mid) 55%, var(--sand-low) 75%, var(--sand-deep) 100%);
  }
  .front-title {
    position: absolute; left: 0; width: 524px; top: 162px; text-align: center;
    font-family: "Playfair Display", serif; font-weight: 600; font-size: 132px; line-height: 1;
  }
  .front-subtitle {
    position: absolute; left: 0; width: 524px; top: 330px; text-align: center;
    font-family: "Open Sans", sans-serif; font-size: 28.5px; letter-spacing: 1px; color: var(--subtitle-brown);
  }
  .front-author {
    position: absolute; left: 0; width: 524px; top: 714px; text-align: center;
    font-family: "Tinos", serif; font-weight: 700; font-size: 23px; letter-spacing: 2.5px; color: var(--white);
  }

  .gold-foil {
    background: linear-gradient(180deg, var(--gold-light) 0%, var(--gold) 35%, var(--gold-dark) 60%, var(--gold) 85%, var(--gold-light) 100%);
    -webkit-background-clip: text; background-clip: text; color: transparent;
  }
</style>
</head>
<body>
<div class="canvas">
  <div class="cover-wrap">

    <section class="back-cover">
      <div class="back-scene" role="img" aria-label="Dark night-blue desert with faint footsteps under a geometric arch border"></div>
      <h2 class="back-title gold-foil">Zīlāta</h2>
      <p class="back-subtitle">Sketches From A Quiet Road</p>
      <p class="keywords">COURAGE. INTEGRITY. FAITH</p>
      <p class="blurb blurb-main">Lorem ipsum dolor sit amet, consectetur adipiscing elit, sed do eiusmod tempor incididunt ut labore et dolore magna aliqua. Quis ipsum suspendisse ultrices gravida. Risus commodo viverra maecenas accumsan lacus vel facili&shy;sis. Lorem ipsum dolor sit amet, consectetur adipiscing elit, sed do eiusmod tempor incididunt ut labore et dolore magna aliqua. Quis ipsum suspendisse ultrices gravida. Risus commodo viverra maecenas accumsan lacus vel fac&shy;ilised do eiusmod sis.</p>
      <div class="author-photo" aria-hidden="true"></div>
      <p class="blurb blurb-side">Lorem ipsum dolor sit amet, consectetur adipiscing elit, sed do eiusmod tempor incididunt ut labore et dolore magna aliqua. Quis ipsum suspendisse ultrices gravida. Risus com&shy;modo viverra maecenas accumsan lacus vel facilisis. Quis ipsum suspendisse ultrices gravida. Risus commodo viverra maecenas accumsan lacus vel facilisis.</p>
      <div class="isbn-box" aria-hidden="true"></div>
    </section>

    <section class="spine">
      <p class="spine-title">Zīlāta</p>
      <p class="spine-arabic" lang="ar">زيلاتة</p>
    </section>

    <section class="front-cover">
      <div class="front-scene" role="img" aria-label="Golden sand dunes with footsteps leading towards a glowing sun, framed by a geometric arch border"></div>
      <h1 class="front-title gold-foil">Zīlāta</h1>
      <p class="front-subtitle">Sketches From A Quiet Road</p>
      <p class="front-author">Idrīs-Wahīd Salmūn Qāzinī</p>
    </section>

  </div>
</div>
</body>
</html>
```